Hollow Marigold Distillery

I need a label designed for my small distillery. I’d like it to have a rose, and the name hollow marigold in script writing. I need the graphic to fit a standard gin bottle and I’ll need to be able to edit it depending on alcohol, warning and descriptions. I want it to look elegant and attractive, but slightly daring too. It’s a 700ml oslo bottle
Target Market(s)
Bespoke gin and vodka drinkers
Industry/Entity Type
Beverage
Font styles to use
Script
Other font styles liked:
- Something easy to read
Requirements
Must have
- Room for me to add and remove text depending on the drink
Nice to have
- Hollow marigold in script, slight colour on the rose and black writing

```html
<!DOCTYPE html>
<html lang="en">
<head>
<meta charset="utf-8">
<title>Hollow Marigold Distillery – Back Label</title>
<link href="https://fonts.googleapis.com/css2?family=Bebas+Neue&display=swap" rel="stylesheet">
<style>
  :root {
    --page: #ffffff;
    --paper: #fbf9f5;
    --paper-edge: #e4e1dc;
    --rose-line: #c98084;
    --ink: #141414;
    --badge-bg: #f6f4f0;
  }
  html, body {
    margin: 0;
    padding: 0;
    width: 1052px;
    height: 1200px;
    overflow: hidden;
    background: var(--page);
  }
  .canvas {
    position: relative;
    width: 1052px;
    height: 1200px;
  }
  .label {
    position: absolute;
    left: 129px;
    top: 169px;
    width: 810px;
    height: 882px;
    background: var(--paper);
    box-shadow: 0 0 0 1px var(--paper-edge);
    font-family: "Bebas Neue", "Oswald", sans-serif;
    color: var(--ink);
  }
  .label__frame {
    position: absolute;
    left: 21px;
    top: 14px;
    right: 15px;
    bottom: 17px;
    border: 3px solid var(--rose-line);
  }
  .description {
    position: absolute;
    left: 100px;
    width: 640px;
    top: 62px;
    text-align: center;
  }
  .description__title {
    margin: 0 0 20px;
    font-size: 27px;
    font-weight: 400;
    letter-spacing: 5px;
  }
  .description__body {
    margin: 0;
    font-size: 20px;
    line-height: 41px;
    letter-spacing: 0.3px;
  }
  .description__body + .description__body {
    margin-top: 41px;
  }
  .description__web {
    margin: 10px 0 0;
    font-size: 28px;
    letter-spacing: 0.5px;
  }
  .certification {
    position: absolute;
    left: 317px;
    top: 606px;
    width: 144px;
    height: 144px;
    background: var(--badge-bg);
  }
  .certification__mark {
    position: absolute;
    left: 28px;
    top: 22px;
    width: 88px;
    height: 88px;
    background: var(--ink);
    border-radius: 50%;
  }
  .icons {
    position: absolute;
    left: 333px;
    top: 748px;
    display: flex;
    gap: 18px;
    align-items: flex-end;
  }
  .producer {
    position: absolute;
    left: 490px;
    width: 262px;
    top: 636px;
    text-align: center;
  }
  .producer__intro {
    margin: 0;
    font-size: 21px;
    letter-spacing: 4px;
    white-space: nowrap;
  }
  .producer__name {
    margin: 6px 0 0;
    font-size: 32px;
    line-height: 42px;
    font-weight: 400;
  }
  .producer__address {
    margin: 2px 0 0;
    font-size: 25px;
  }
</style>
</head>
<body>
<div class="canvas">
  <section class="label">
    <div class="label__frame"></div>

    <div class="description">
      <h2 class="description__title">Description</h2>
      <p class="description__body">Lorem ipsum dolor sit amet. Est officiis perferendis et aliquid nulla qui dicta quia eum aspernatur odit et ducimus blanditiis. Qui quaerat expedita aut perferendis illum ea sapiente sunt rem voluptas mollitia. Sed accusamus neque in tempora deleniti ex sapiente dignissimos et temporibus corrupti. Est commodi blanditiis expedita sit dolorum tempora eos reiciendis perferendis sed repudiandae iure commodi nostrum in doloremque corrupti.</p>
      <p class="description__body">Eos dicta autem sed facilis distinctio qui modi ipsum!<br>Sed dicta culpa qui ipsum quia aut voluptas sint qui eius laudantium. Quo eligendi voluptatem et omnis perferendis aut tempora odio.</p>
      <p class="description__web">www.hollowmarigold.com</p>
    </div>

    <div class="certification" role="img" aria-label="Origin certification badge">
      <div class="certification__mark"></div>
    </div>

    <div class="icons">
      <svg class="icons__recycle" width="48" height="46" viewBox="0 0 48 46" role="img" aria-label="Recyclable">
        <g fill="none" stroke="#141414" stroke-width="6" stroke-linejoin="round">
          <path d="M14 18 L22 5 L30 18"/>
          <path d="M38 22 L44 36 L28 38"/>
          <path d="M18 40 L4 38 L11 26"/>
        </g>
        <g fill="#141414">
          <polygon points="26,22 38,20 36,10"/>
          <polygon points="30,42 24,32 22,44"/>
          <polygon points="6,20 16,28 16,16"/>
        </g>
      </svg>
      <svg class="icons__units" width="30" height="58" viewBox="0 0 30 58" role="img" aria-label="7.5 standard units">
        <path d="M11 0 h8 v9 c0 3 11 6 11 16 v29 q0 4 -4 4 h-22 q-4 0 -4 -4 v-29 c0 -10 11 -13 11 -16 z" fill="#141414"/>
        <text x="15" y="35" text-anchor="middle" font-family="Arial, sans-serif" font-weight="700" font-size="10" fill="#fbf9f5">7.5</text>
        <text x="15" y="44" text-anchor="middle" font-family="Arial, sans-serif" font-weight="700" font-size="5" fill="#fbf9f5">UNITS</text>
      </svg>
    </div>

    <div class="producer">
      <p class="producer__intro">Produced and botlled by</p>
      <h3 class="producer__name">Hollow Marigold<br>Distillery</h3>
      <p class="producer__address">Address, Australia</p>
    </div>
  </section>
</div>
</body>
</html>
```